Birchline Septic Solutions

Would like to see some single sided ones but would also like to see some double sided with one sided only being the logo. Owners name is Colin Vandro. Phone number is 555-214-0387
Services are pumping, inspections, installs, and repairs

Contact Information for Business Card

555-241-0387 Colin Vandro Larkfield, OH

```html
<!DOCTYPE html>
<html lang="en">
<head>
<meta charset="utf-8">
<title>Birchline Septic Solutions – Business Cards</title>
<link href="https://fonts.googleapis.com/css2?family=Arimo:wght@400;700&display=swap" rel="stylesheet">
<style>
  :root {
    --bg: #e9e9e9;
    --card: #ffffff;
    --ink: #2b2b2b;
    --muted: #8a8a8a;
    --teal: #2bb5aa;
    --ghost: #ececec;
  }
  * { box-sizing: border-box; margin: 0; padding: 0; }
  html, body { width: 1200px; height: 802px; overflow: hidden; }
  body {
    background: var(--bg);
    font-family: "Arimo", Arial, sans-serif;
    display: flex;
    align-items: center;
    justify-content: center;
    gap: 60px;
  }
  .card {
    position: relative;
    width: 520px;
    height: 297px;
    background: var(--card);
    border-bottom: 5px solid var(--teal);
    box-shadow: 0 8px 24px rgba(0,0,0,0.12);
    overflow: hidden;
  }
  .card__scenery {
    position: absolute;
    right: 0;
    bottom: 0;
    width: 190px;
    height: 200px;
    background: linear-gradient(160deg, rgba(236,236,236,0) 0%, var(--ghost) 55%, #e4e4e4 100%);
  }
  .brand {
    display: flex;
    align-items: center;
    gap: 10px;
    color: var(--ink);
    font-weight: 700;
    text-transform: uppercase;
    letter-spacing: 0.04em;
    line-height: 1.1;
  }
  .brand__mark {
    width: 14px;
    height: 14px;
    background: var(--teal);
    flex: none;
  }
  .front .brand {
    position: absolute;
    left: 40px;
    top: 110px;
    font-size: 24px;
  }
  .owner {
    position: absolute;
    right: 40px;
    top: 34px;
    text-align: right;
  }
  .owner__name {
    color: var(--teal);
    font-weight: 700;
    font-size: 22px;
    letter-spacing: 0.01em;
  }
  .owner__role {
    color: var(--muted);
    font-size: 14px;
    margin-top: 2px;
  }
  .owner__tab {
    position: absolute;
    right: -40px;
    top: 2px;
    width: 18px;
    height: 22px;
    background: var(--teal);
  }
  .contact {
    position: absolute;
    left: 40px;
    bottom: 44px;
    font-size: 15px;
    line-height: 1.6;
  }
  .contact__city { color: var(--muted); }
  .contact__phone {
    display: flex;
    align-items: center;
    gap: 6px;
    color: var(--ink);
    font-weight: 700;
  }
  .contact__phone svg { width: 13px; height: 13px; }
  .back {
    display: flex;
    align-items: center;
    justify-content: center;
    padding: 0 30px;
  }
  .back .brand { font-size: 25px; white-space: nowrap; }
</style>
</head>
<body>
  <section class="card front">
    <div class="card__scenery" role="img" aria-label="Faint grey mountain and pine tree landscape"></div>
    <div class="owner">
      <span class="owner__tab"></span>
      <div class="owner__name">COLIN VANDRO</div>
      <div class="owner__role">Owners</div>
    </div>
    <div class="brand"><span class="brand__mark"></span>Birchline<br>Septic Solutions</div>
    <div class="contact">
      <div class="contact__city">Larkfield, OH</div>
      <div class="contact__phone">
        <svg viewBox="0 0 24 24" aria-hidden="true"><circle cx="12" cy="12" r="11" fill="none" stroke="#2bb5aa" stroke-width="3"/><path d="M8 7l2 0 1 3-1.5 1a6 6 0 0 0 3.5 3.5l1-1.5 3 1 0 2c-5 1-10-4-9-9z" fill="#2bb5aa"/></svg>
        555-214-0387
      </div>
    </div>
  </section>
  <section class="card back">
    <div class="brand"><span class="brand__mark"></span>Birchline Septic Solutions</div>
  </section>
</body>
</html>
```